TalkHarbor - Language Coaching Services

Sleek, innovative, trendy design for Language Coaching business.

TalkHarbor is a new UK based company that provides Language Coaching services. We offer highly personalized on-line and face to face language courses. We also impart learning techniques workshops based on the latest neuroscience research for second-language acquisition.

Target Market(s)

See attached info

Industry/Entity Type

Consulting

Contact Information for Business Card

TalkHarbor
DaniaKV@talkharbor.co.uk
TalkHarbor.co.uk
London, UK

Font styles to use
Sans Serif

```html
<!DOCTYPE html>
<html lang="en">
<head>
<meta charset="utf-8">
<title>TalkHarbor Business Card</title>
<link href="https://fonts.googleapis.com/css2?family=Montserrat:wght@400;500;700&display=swap" rel="stylesheet">
<style>
  :root {
    --backdrop: #3b3b3b;
    --card-dark: #1f1f1f;
    --card-dark-edge: #2a2a2a;
    --mark-dark: #0c0c0c;
    --ring-dark: #6e6e6e;
    --card-light: #f3f3f3;
    --brand-blue: #1a8cc4;
    --brand-navy: #16618f;
    --ink: #3d3d3d;
    --muted: #5a5a5a;
    --divider: #444444;
  }
  * { margin: 0; padding: 0; box-sizing: border-box; }
  html, body { width: 1200px; height: 895px; overflow: hidden; }
  body {
    background: var(--backdrop);
    font-family: "Montserrat", sans-serif;
    position: relative;
  }
  .card {
    position: absolute;
    width: 560px;
    height: 320px;
    border-radius: 22px;
    box-shadow: 0 14px 30px rgba(0,0,0,0.45);
  }
  .card-front {
    left: 60px; top: 100px;
    background: linear-gradient(160deg, var(--card-dark-edge), var(--card-dark));
    display: flex; flex-direction: column; align-items: center; justify-content: center; gap: 22px;
  }
  .front-ring {
    width: 96px; height: 96px; border-radius: 50%;
    border: 7px solid var(--ring-dark);
  }
  .front-name {
    font-weight: 700; font-size: 40px; letter-spacing: 1px;
    color: var(--mark-dark);
  }
  .card-back {
    left: 580px; top: 475px;
    background: linear-gradient(180deg, #f8f8f8, var(--card-light));
  }
  .brand-block {
    position: absolute; left: 30px; top: 92px; width: 250px;
    display: flex; flex-direction: column; align-items: center; gap: 14px;
  }
  .brand-ring {
    width: 88px; height: 88px; border-radius: 50%;
    border: 6px solid var(--brand-blue);
  }
  .brand-name {
    font-weight: 700; font-size: 30px; letter-spacing: 0.5px;
    color: var(--brand-blue);
  }
  .divider {
    position: absolute; left: 292px; top: 60px;
    width: 1.5px; height: 200px; background: var(--divider);
  }
  .details { position: absolute; left: 318px; top: 62px; }
  .person-name {
    font-weight: 700; font-size: 26px; color: var(--brand-navy); letter-spacing: 0.5px;
  }
  .person-role { font-size: 13px; color: var(--muted); margin-top: 2px; }
  .contact-list { list-style: none; margin-top: 18px; }
  .contact-list li {
    display: flex; align-items: center; gap: 10px;
    font-size: 12.5px; color: var(--ink); margin-bottom: 9px;
  }
  .contact-list li.gap { margin-top: 18px; }
  .contact-list svg { width: 14px; height: 14px; fill: var(--brand-blue); flex: none; }
</style>
</head>
<body>
  <div class="card card-front">
    <div class="front-ring"></div>
    <div class="front-name">TALKHARBOR</div>
  </div>

  <div class="card card-back">
    <div class="brand-block">
      <div class="brand-ring"></div>
      <div class="brand-name">TALKHARBOR</div>
    </div>
    <div class="divider"></div>
    <div class="details">
      <div class="person-name">DANIA KV</div>
      <div class="person-role">Founder &amp; CEO</div>
      <ul class="contact-list">
        <li>
          <svg viewBox="0 0 24 24" aria-hidden="true"><path d="M12 2a7 7 0 0 0-7 7c0 5 7 13 7 13s7-8 7-13a7 7 0 0 0-7-7zm0 9.5A2.5 2.5 0 1 1 12 6.5a2.5 2.5 0 0 1 0 5z"/></svg>
          London, UK
        </li>
        <li class="gap">
          <svg viewBox="0 0 24 24" aria-hidden="true"><path d="M6.6 10.8a15 15 0 0 0 6.6 6.6l2.2-2.2a1 1 0 0 1 1-.25 11.4 11.4 0 0 0 3.6.57 1 1 0 0 1 1 1V20a1 1 0 0 1-1 1A17 17 0 0 1 3 4a1 1 0 0 1 1-1h3.5a1 1 0 0 1 1 1c0 1.25.2 2.45.57 3.6a1 1 0 0 1-.25 1z"/></svg>
          020 7946 0321
        </li>
        <li>
          <svg viewBox="0 0 24 24" aria-hidden="true"><path d="M2 5h20v14H2zm2 2v.5l8 5 8-5V7z"/></svg>
          DaniaKV@talkharbor.co.uk
        </li>
        <li>
          <svg viewBox="0 0 24 24" aria-hidden="true"><circle cx="12" cy="12" r="10"/></svg>
          www.TalkHarbor.co.uk
        </li>
      </ul>
    </div>
  </div>
</body>
</html>
```